Business Cards for company that supports physicians that do medical research

Need to create a business card for Qorvel Studies (www.qorvelstudies.example), a company devoted to supporting physicians who conduct medical research. The form of the card should match the message of research and information quest. I have provided the logo of the company as an uploaded file. Designs should be simple and slick aimed at very high end clients.

Target Market(s)

Medical doctors that are also researchers

Industry/Entity Type

Medical

Contact Information for Business Card

Should feature logo and fields for personal info:
Name/title
Phone /email

Font styles to use
Serif
Sans Serif

Requirements
Must have
• Qorvel logo and fields for personal info:
• Name: Bertrand Okonfu
• Title: VP Research and Senior Analyst
• Phone: 555-203-4719
• email: info@qorvelstudies.example
Nice to have
• Interesting cards that I've seen:
• 1- all black/charcoal or very dark background
• 2- Plastic - semi-transparent
• 3- non-standard height-width ratios
• 4- Functional cards -- USB drive incorporated
Should not have
• Too busy; needs to stay very simple

```html
<!DOCTYPE html>
<html lang="en">
<head>
<meta charset="utf-8">
<title>Qorvel Studies – Business Card</title>
<link href="https://fonts.googleapis.com/css2?family=Open+Sans:ital,wght@0,400;0,600;1,400&display=swap" rel="stylesheet">
<style>
  :root {
    --stage: #3a3a3a;
    --card-white: #f7f7f7;
    --brand-blue: #1b7bbd;
    --brand-green: #3fae49;
    --ink: #333333;
    --rule: #c9c9c9;
    --white: #ffffff;
  }
  * { box-sizing: border-box; margin: 0; padding: 0; }
  html, body {
    width: 1200px; height: 750px; overflow: hidden;
    background: var(--stage);
    font-family: "Open Sans", Arial, sans-serif;
  }
  .canvas { position: relative; width: 1200px; height: 750px; }
  .card {
    position: absolute; top: 228px; width: 461px; height: 263px; overflow: hidden;
  }
  .card--front { left: 124px; background: var(--card-white); }
  .card--back { left: 618px; background: var(--brand-blue); }

  .brand-name {
    position: absolute; left: 42px; top: 88px; width: 175px;
    font-weight: 600; font-size: 34px; line-height: 38px;
    color: var(--brand-green);
  }
  .divider {
    position: absolute; left: 230px; top: 80px; width: 1px; height: 96px;
    background: var(--rule);
  }
  .contact { position: absolute; left: 253px; top: 88px; }
  .contact__name { font-weight: 600; font-size: 16px; color: var(--brand-blue); line-height: 20px; }
  .contact__title { font-size: 12px; color: var(--brand-green); line-height: 16px; margin-bottom: 9px; }
  .contact__line {
    display: flex; align-items: center; gap: 6px;
    font-size: 11px; color: var(--ink); line-height: 18px;
  }
  .contact__line svg { width: 11px; height: 11px; flex: none; }

  .front-swoosh { position: absolute; left: 0; bottom: 0; width: 461px; height: 263px; }
  .front-url {
    position: absolute; left: 0; width: 100%; top: 240px; text-align: center;
    font-style: italic; font-size: 11px; letter-spacing: 2.6px; color: var(--white);
  }

  .back-brand { position: absolute; right: 26px; top: 150px; text-align: left; width: 150px; }
  .back-brand__name {
    font-weight: 600; font-size: 28px; line-height: 30px; color: var(--white);
  }
  .back-brand__url {
    margin-top: 8px; font-style: italic; font-size: 10.5px; letter-spacing: 1.2px; color: var(--white);
    white-space: nowrap;
  }
</style>
</head>
<body>
<main class="canvas">
  <section class="card card--front">
    <div class="brand-name">Qorvel Studies</div>
    <div class="divider"></div>
    <div class="contact">
      <div class="contact__name">Bertrand Okonfu</div>
      <div class="contact__title">VP Research &amp; Senior Analyst</div>
      <div class="contact__line">
        <svg viewBox="0 0 24 24" aria-hidden="true"><path fill="#1b7bbd" d="M6.6 10.8a15.2 15.2 0 0 0 6.6 6.6l2.2-2.2c.3-.3.7-.4 1-.2 1.1.4 2.3.6 3.6.6.6 0 1 .4 1 1V20c0 .6-.4 1-1 1A17 17 0 0 1 3 4c0-.6.4-1 1-1h3.5c.6 0 1 .4 1 1 0 1.3.2 2.5.6 3.6.1.3 0 .7-.2 1z"/></svg>
        <span>555-203-4719</span>
      </div>
      <div class="contact__line">
        <svg viewBox="0 0 24 24" aria-hidden="true"><rect x="2" y="5" width="20" height="14" fill="#1b7bbd"/><path d="M2 5l10 8 10-8" fill="none" stroke="#ffffff" stroke-width="1.8"/></svg>
        <span>info@qorvelstudies.example</span>
      </div>
    </div>
    <svg class="front-swoosh" viewBox="0 0 461 263" aria-hidden="true">
      <path d="M0 263 L0 259 Q230.5 212 461 259 L461 263 Z" fill="#1b7bbd"/>
      <path d="M0 256 Q230.5 199 461 256" fill="none" stroke="#3fae49" stroke-width="3"/>
    </svg>
    <div class="front-url">www.qorvelstudies.example</div>
  </section>

  <section class="card card--back">
    <div class="back-brand">
      <div class="back-brand__name">Qorvel Studies</div>
      <div class="back-brand__url">www.qorvelstudies.example</div>
    </div>
  </section>
</main>
</body>
</html>
```